New Business Card for Software Company

We are looking at rebranding a 10 year old company that specializes in PDF and DWF solutions for Architects and Engineers. We will attach the new company logo that we are going with so you can work with that and complimentary colors.
The sample information we would like on the business card is:
Gerald Pinfold
Vice President
4738 W. Harrowgate Lane. STE 305
PMB#417
Dunmere, AZ 85374
866-392-5074 US Toll Free
123-456-3190 Cell
gpinfold@plavorix.com
The old tag line that we had on the business cars was.
Delivering precise document and drawing tools to architects and engineers worldwide.
If you have an idea for a better tag line we are open to that also.
Updates
We would like to thank all of the Designers for their wonderful work. We apologize that we will not have the time to provide feedback to everyone. There is just so many innovative and professional designs that you have all created making our decision even harder.
Target Market(s)
Architects and Engineers
Industry/Entity Type
Business
Look and feel

```html
<!DOCTYPE html>
<html lang="en">
<head>
<meta charset="utf-8">
<title>Plavorix Business Card</title>
<link rel="stylesheet" href="https://fonts.googleapis.com/css2?family=Open+Sans:wght@400;600;700;800&display=swap">
<style>
  :root {
    --bg: #e9e7e3;
    --card: #ffffff;
    --orange: #ef5a24;
    --orange-light: #f5a12a;
    --red: #c8232c;
    --ink: #4a4a4a;
    --ink-soft: #6b6b6b;
    --rule: #b9b9b9;
  }
  * { box-sizing: border-box; margin: 0; padding: 0; }
  html, body { width: 1200px; height: 720px; overflow: hidden; }
  body {
    background: var(--bg);
    font-family: "Open Sans", Arial, sans-serif;
    position: relative;
  }
  .card {
    position: absolute;
    width: 520px;
    height: 297px;
    background: var(--card);
    box-shadow: 0 6px 18px rgba(0,0,0,0.18);
    overflow: hidden;
  }
  .card--front { left: 50px; top: 150px; }
  .card--back  { left: 630px; top: 273px; }

  /* Front */
  .front-band {
    position: absolute; left: 0; top: 0; bottom: 0; width: 92px;
    background: linear-gradient(170deg, var(--orange-light) 0%, var(--orange) 40%, var(--red) 100%);
  }
  .front-divider {
    position: absolute; left: 100px; top: 0; bottom: 0; width: 1px;
    background: var(--rule);
  }
  .brand-dot {
    position: absolute; border-radius: 50%;
    background: var(--orange);
    border: 6px solid var(--card);
  }
  .card--front .brand-dot { left: 58px; top: 34px; width: 62px; height: 62px; }
  .wordmark {
    position: absolute;
    font-weight: 800;
    color: var(--orange);
    letter-spacing: -1px;
    line-height: 1;
  }
  .card--front .wordmark { left: 132px; top: 36px; font-size: 50px; }
  .person {
    position: absolute; right: 34px; top: 112px; text-align: right;
  }
  .person-name { font-weight: 700; font-size: 15px; color: var(--orange); }
  .person-title { font-size: 12px; color: var(--ink-soft); }
  .contact {
    position: absolute; left: 124px; top: 160px;
    list-style: none; font-size: 12.5px; color: var(--ink); line-height: 20px;
  }
  .contact li { display: flex; align-items: center; gap: 7px; }
  .contact svg { width: 11px; height: 11px; fill: var(--orange); flex: none; }
  .contact .address { display: block; margin-top: 4px; }

  /* Back */
  .back-brand {
    position: absolute; left: 0; right: 0; top: 92px;
    display: flex; justify-content: center; align-items: center; gap: 12px;
  }
  .card--back .brand-dot { position: static; width: 70px; height: 70px; border: none; }
  .card--back .wordmark { position: static; font-size: 58px; }
  .tagline {
    position: absolute; left: 0; right: 0; top: 200px;
    text-align: center; text-transform: uppercase;
    font-size: 14.5px; font-weight: 400; color: var(--ink);
    line-height: 21px; letter-spacing: 0.2px;
  }
</style>
</head>
<body>
  <section class="card card--front" aria-label="Business card front">
    <div class="front-band"></div>
    <div class="front-divider"></div>
    <div class="brand-dot"></div>
    <div class="wordmark">Plavorix</div>
    <div class="person">
      <div class="person-name">Gerald Pinfold</div>
      <div class="person-title">Vice President</div>
    </div>
    <ul class="contact">
      <li><svg viewBox="0 0 12 12"><path d="M2.5 0.5l2 2.2-1.1 1.6c.7 1.6 2 2.9 3.6 3.6l1.6-1.1 2.2 2-1.3 2.2C4.9 10.6 1.4 7.1.3 1.8z"/></svg>866-392-5074US(TF)</li>
      <li><svg viewBox="0 0 12 12"><path d="M3 0h6a1 1 0 0 1 1 1v10a1 1 0 0 1-1 1H3a1 1 0 0 1-1-1V1a1 1 0 0 1 1-1zm.5 1.5v7h5v-7zM6 9.5a.8.8 0 1 0 0 1.6.8.8 0 0 0 0-1.6z"/></svg>123-456-3190</li>
      <li><svg viewBox="0 0 12 12"><path d="M0 2h12v8H0zm1 1v.4l5 3.2 5-3.2V3zm0 1.6V9h10V4.6L6 7.8z"/></svg>gpinfold@plavorix.com</li>
      <li class="address">4738 W. Harrowgate Lane. STE 305<br>PMB#417, Dunmere, AZ 85374</li>
    </ul>
  </section>

  <section class="card card--back" aria-label="Business card back">
    <div class="back-brand">
      <div class="brand-dot"></div>
      <div class="wordmark">Plavorix</div>
    </div>
    <p class="tagline">Delivering precise document and drawing<br>tools to architects and engineers worldwide</p>
  </section>
</body>
</html>
```